Generate website for parcelnook.com

Please design a website for our business. It must be clean, streamlined and obvious.

Our business combines ecommerce, with social networking, and zorvi maps. The logo is a shopping bag (ecommerce) and honeycombs inside representing the various compartments of business that are offered throughout site.

Clients use our site to visit the interior of stores and restaurants through video streaming and can virtually "walk through" the store and purchase items with friends and loved ones through the web.

We want to incorporate this logo with the work that we are doing and play on this honeycomb theme.

Our business is "parcelnook.com" because we are all about "u"!

Please make homepage with about us tab, contact us form, mission tab, we also want a page with our research links included that bolster the case for our startup.

We will incorporate a small video on the front screen. A homepage like fildrawer.com only this time with our parcelnook!

Also include, COMING SOON, on the homepage please.
Updates

These are some good templates/example sites of clean and simple but effective: https://7elmrow.com/preview www.fildrawer.com

We are excited to see your submissions. Currently, a very good and only one designer has posted so far. Let us know!

Please include the TM (trademark) symbol after the logo, the name, and the slogan throughout the website. Thank you!

Put the TM after the LOGO and after the slogan "Placement ran Supreme" Lorcan

Target Market(s)

We will begin with female online shoppers.

Industry/Entity Type

Shopping

Font styles to use
Serif
Sans Serif

Colors
e567a6
fece3e
85cae6

Requirements
Must have
• Clean Look
Simple like Fildrawer with simple options "see film" or login/signup.

With browser tabs at the bottom much like fildrawer.

1. Shopper when opening Parcelnook.com website will see a simple webpage with a large Parcelnook logo in the center.

2. User will see log-in and password or create account in upper right hand corner of webpage. Mobile device website will be underneath logo.

3.We Prefer a background for webpages adding a softer experience on the the eyes of the user. A photo in the background to show shopretail experience.

4. Clicking on theParcelnook logo will inform users of details and instructions about platform. Example: About, contact, mission, Help etc. Logo will become somewhat like an interactive tool for help and guidance.

5. Parcelnook is currently scouting for it's founding venues. A founding venue will be the first venues to appear to the public on the Parcelnook platform. Founding venues (FV) will inherit a lifetime of the lowest possible rates of 2%* for the duration of it's business. All businesses wishing to participate in the founding venues offer please leave your email address and store name and a representative will get back with you.

*Venues will be subjected to credit card and CoinTrail rates in addition.

Nice to have
• http://www.zorvi.com/patents/US5193774

Must include the link above/visual of this page on the site as well.

```html
<!DOCTYPE html>
<html lang="en">
<head>
<meta charset="utf-8">
<title>Parcelnook — Shop and walk with friends through the aisles</title>
<link rel="stylesheet" href="https://fonts.googleapis.com/css2?family=Carlito&family=Questrial&display=swap">
<style>
  :root{
    --ink:#000000;
    --paper:#ffffff;
    --panel:rgba(255,255,255,0.68);
    --card:rgba(255,255,255,0.32);
    --card-edge:rgba(255,255,255,0.95);
    --heading:#111111;
    --muted:#4a4a4a;
    --brand-grey:#6a6a6a;
    --brand-mark:#9b59b6;
    --btn-top:#ff9c8a;
    --btn-mid:#ff6f5b;
    --btn-bottom:#ff9f8f;
    --rule:#8a8a8a;
    --scene-dark:#2a1d18;
    --scene-warm:#b07a45;
    --scene-glow:#e6b777;
  }
  *{margin:0;padding:0;box-sizing:border-box;}
  html,body{width:1200px;height:1091px;overflow:hidden;background:var(--ink);}
  .page{position:relative;width:1200px;height:1091px;overflow:hidden;background:var(--ink);font-family:"Carlito",sans-serif;}

  .site-nav{position:absolute;left:0;top:0;width:1200px;height:136px;background:var(--ink);}
  .site-nav a{position:absolute;top:56px;transform:translateX(-50%);color:var(--paper);text-decoration:none;font-family:Arial,"Helvetica",sans-serif;font-size:20px;white-space:nowrap;}

  .storefront{position:absolute;left:0;top:136px;width:1200px;height:791px;
    background:
      radial-gradient(ellipse 420px 260px at 420px 180px,rgba(230,183,119,0.75),transparent 70%),
      radial-gradient(ellipse 300px 300px at 1050px 300px,rgba(210,190,170,0.55),transparent 70%),
      radial-gradient(ellipse 500px 140px at 350px 700px,rgba(60,50,90,0.8),transparent 70%),
      linear-gradient(180deg,var(--scene-warm) 0%,#8a6a55 45%,var(--scene-dark) 100%);}

  .hero-panel{position:absolute;left:0;top:256px;width:1200px;height:515px;background:var(--panel);}

  .brand{position:absolute;left:316px;top:280px;display:flex;align-items:flex-end;}
  .brand-mark{width:124px;height:140px;background:var(--brand-mark);}
  .brand-name{position:absolute;left:148px;top:58px;font-family:"Questrial",sans-serif;font-size:72px;line-height:1;color:var(--brand-grey);white-space:nowrap;}
  .slogan{position:absolute;left:0;width:1182px;top:443px;text-align:center;font-family:"Questrial",sans-serif;font-size:25px;color:var(--heading);}

  .divider{position:absolute;left:616px;top:505px;width:2px;height:242px;background:var(--paper);}

  .invite{position:absolute;top:506px;width:420px;transform:translateX(-50%);text-align:center;font-size:31px;line-height:42px;color:var(--heading);}
  .invite--shopper{left:395px;}
  .invite--store{left:851px;}

  .enroll-card{position:absolute;top:611px;width:379px;height:142px;border:2px solid var(--card-edge);border-radius:10px;background:var(--card);}
  .enroll-card--shopper{left:188px;}
  .enroll-card--store{left:659px;}
  .enroll-card p{position:absolute;left:0;width:100%;top:9px;text-align:center;font-size:31px;}
  .enroll-card--shopper p{color:var(--muted);}
  .enroll-card--store p{color:var(--heading);}

  .enroll-button{position:absolute;top:49px;height:67px;border:1px solid rgba(255,255,255,0.8);
    background:linear-gradient(180deg,var(--btn-top) 0%,var(--btn-mid) 50%,var(--btn-bottom) 100%);
    box-shadow:2px 3px 4px rgba(0,0,0,0.45);color:var(--paper);font-family:"Carlito",sans-serif;font-size:20px;
    display:flex;align-items:center;justify-content:center;}
  .enroll-card--shopper .enroll-button{left:31px;width:311px;}
  .enroll-card--store .enroll-button{left:62px;width:256px;}

  .site-footer{position:absolute;left:0;top:927px;width:1200px;height:164px;background:var(--ink);color:var(--paper);}
  .founding-offer{position:absolute;left:0;width:1200px;text-align:center;font-family:Arial,"Helvetica",sans-serif;font-size:21px;word-spacing:18px;line-height:32px;top:39px;}
  .footer-rule{position:absolute;left:63px;top:110px;width:1096px;height:1px;background:var(--rule);}
  .legal{position:absolute;left:0;width:1200px;top:122px;text-align:center;font-family:"Questrial",sans-serif;font-size:13.5px;}
</style>
</head>
<body>
<div class="page">
  <nav class="site-nav">
    <a href="#" style="left:175px">About us</a>
    <a href="#" style="left:425px">Mission</a>
    <a href="#" style="left:756px">Coming soon</a>
    <a href="#" style="left:1023px">Contact us</a>
  </nav>

  <div class="storefront" role="img" aria-label="Blurred night-time photograph of a lit boutique storefront window with string lights"></div>

  <section class="hero-panel" aria-label="Welcome"></section>

  <div class="brand">
    <div class="brand-mark"></div>
    <span class="brand-name">Parcelnook</span>
  </div>
  <p class="slogan">Shop and walk with friends through the aisles</p>

  <div class="divider"></div>

  <h2 class="invite invite--shopper" style="font-weight:400">Sign up to Join the Shopping Experience</h2>
  <h2 class="invite invite--store" style="font-weight:400">Request or Become a participating store</h2>

  <div class="enroll-card enroll-card--shopper">
    <p>Enroll here to shop</p>
    <div class="enroll-button">Enter Your Email Address</div>
  </div>
  <div class="enroll-card enroll-card--store">
    <p>Enroll or nominate a shop</p>
    <div class="enroll-button">Store Information</div>
  </div>

  <footer class="site-footer">
    <p class="founding-offer">FOUNDIG VENUES WILL INHERIT A 2% LIFETIME FEE*<br>LIMITED TO A SELECT FEW</p>
    <div class="footer-rule"></div>
    <p class="legal">©2014 · Parcelnook.com LLC. All Rights Reserved. Under Use and Authority of Uspto Patent# 5193774.</p>
  </footer>
</div>
</body>
</html>
```